Figure for presentation on a hybrid research project

We need a figure that shows a series of 6 technical projects feeding into 3 multidisciplinary hybrid projects.
The concept is a ring of 6 technical projects, which could look like a 6 colour swirl (see
https://en.plorvanex.org/wiki/Vector_graphics for an example of a 4 colour swirl.)
The 3 hybrid projects sit in the centre because they rely on input from many of the surrounding technical projects.
I've drawn a rough version in Powerpoint - see attached file uploaded. Note, in my example I couldn't draw the swirling outer ring and the colour selection is poor. The acronym for the overall Centre using the figure is VexORDA, so we will have a mint leaf and turquoise green in the logo, plus also nerves, since we will be researching neural interconnections.
We ABSOLUTELY NEED the final form of the figure to include vector graphics formats (including a form that can be edited in Photoshop) because we may need to change the title of the technical projects or of the hybrid projects at short notice ourselves.

Target Market(s)

Academic: eminent scientists and engineers

Industry/Entity Type

Technical

Font styles to use
Sans Serif

Colors
04a990

Requirements
Must have
• The projects around the ring with all project titles legible; the final figure will be reduced to no more than 8cm x 8cm in the proposal (probably less).
• Only one colour selected, because we have included that colour in the logo that we are having designed. Otherwise, a colour series around the ring that is pleasant, and another compatible colour series for the inter 3 projects.
• We ABSOLUTELY NEED the final form of the figure to include vector graphics formats (including a form that can be edited in Photoshop) because we may need to change the title of the technical projects or of the hybrid projects at short notice ourselves.
Nice to have
• See the figure we uploaded; that's the essence
• HOWEVER VIP: two of the titles around the outer ring have changed slightly.
• Computational Modelling is now Neuronal Modelling and
• Signal Processing is now Non-Invasive Interfaces (note that I've now changed the titles on the uploaded figure)

```html
<!DOCTYPE html>
<html lang="en">
<head>
<meta charset="utf-8">
<title>VexORDA research programme figure</title>
<link rel="stylesheet" href="https://fonts.googleapis.com/css2?family=Montserrat:wght@700;800&display=swap">
<style>
  :root {
    --brand-teal: #04a990;
    --petal-light: #0aa38a;
    --petal-mid: #079a80;
    --petal-dark: #067a5f;
    --ring-dark: #06795e;
    --core: #08a68d;
    --line: #ffffff;
    --text: #ffffff;
    --page: #ffffff;
  }
  html, body {
    margin: 0;
    padding: 0;
    width: 1200px;
    height: 999px;
    overflow: hidden;
    background: var(--page);
  }
  .programme-figure {
    display: block;
    width: 1200px;
    height: 999px;
  }
  .petal { stroke: var(--line); stroke-width: 5; }
  .petal--light { fill: var(--petal-light); }
  .petal--mid { fill: var(--petal-mid); }
  .petal--dark { fill: var(--petal-dark); }
  .project-title {
    font-family: "Montserrat", sans-serif;
    font-weight: 700;
    font-size: 22px;
    fill: var(--text);
    letter-spacing: 0.3px;
  }
  .hybrid-ring { fill: var(--ring-dark); stroke: var(--line); stroke-width: 5; }
  .hybrid-divider { fill: none; stroke: var(--line); stroke-width: 6; stroke-linejoin: miter; }
  .hybrid-title {
    font-family: "Montserrat", sans-serif;
    font-weight: 800;
    font-size: 40px;
    fill: var(--text);
    letter-spacing: 1px;
  }
  .centre-core { fill: var(--core); stroke: var(--line); stroke-width: 6; }
  .centre-name {
    font-family: "Montserrat", sans-serif;
    font-weight: 800;
    font-size: 30px;
    fill: var(--text);
    text-anchor: middle;
  }
</style>
</head>
<body>
<svg class="programme-figure" viewBox="0 0 1130 940" xmlns="http://www.w3.org/2000/svg" aria-label="Six technical projects surrounding three hybrid projects">
  <defs>
    <filter id="ring-shadow" x="-30%" y="-30%" width="160%" height="160%">
      <feDropShadow dx="0" dy="0" stdDeviation="14" flood-color="#003d30" flood-opacity="0.45"/>
    </filter>

    <path id="path-living" d="M 295 288 Q 400 218 532 232"/>
    <path id="path-gene" d="M 492 135 Q 710 125 762 358"/>
    <path id="path-electro" d="M 775 610.6 A 212 212 0 0 0 790.6 253.3"/>
    <path id="path-optrode" d="M 556 730 Q 700 772 832 694"/>
    <path id="path-neuronal" d="M 335 610 Q 372 762 518 820"/>
    <path id="path-noninvasive" d="M 282 664 Q 255 470 368 350"/>

    <path id="path-connect" d="M 600.6 326.4 A 157 157 0 0 1 716.4 491.7"/>
    <path id="path-act" d="M 405.4 505.3 A 157 157 0 0 1 506.3 330.5"/>
    <path id="path-perceive" d="M 416 598.8 A 188 188 0 0 0 722.8 572"/>
  </defs>

  <g class="technical-swirl">
    <circle class="petal petal--mid" cx="658.3" cy="546.8" r="245"/>
    <circle class="petal petal--dark" cx="668.8" cy="427.3" r="245"/>
    <circle class="petal petal--light" cx="570.5" cy="358.5" r="245"/>
    <circle class="petal petal--dark" cx="461.7" cy="409.2" r="245"/>
    <circle class="petal petal--light" cx="451.2" cy="528.7" r="245"/>
    <circle class="petal petal--dark" cx="549.5" cy="597.5" r="245"/>
  </g>

  <g class="technical-titles">
    <text class="project-title"><textPath href="#path-living" startOffset="50%" text-anchor="middle">Living Electrodes</textPath></text>
    <text class="project-title"><textPath href="#path-gene" startOffset="50%" text-anchor="middle">Gene Regulated Interfaces</textPath></text>
    <text class="project-title"><textPath href="#path-electro" startOffset="50%" text-anchor="middle">Electro-modulated Interfaces</textPath></text>
    <text class="project-title"><textPath href="#path-optrode" startOffset="50%" text-anchor="middle">Optrode Interfaces</textPath></text>
    <text class="project-title"><textPath href="#path-neuronal" startOffset="50%" text-anchor="middle">Neuronal Modelling</textPath></text>
    <text class="project-title"><textPath href="#path-noninvasive" startOffset="50%" text-anchor="middle">Non-invasive Interfaces</textPath></text>
  </g>

  <g class="hybrid-cycle">
    <circle class="hybrid-ring" cx="560" cy="478" r="210" filter="url(#ring-shadow)"/>
    <polyline class="hybrid-divider" points="502,276 542.4,310.9 525.5,357.9"/>
    <polyline class="hybrid-divider" points="763.7,528.8 713.5,546.3 681.3,508.2"/>
    <polyline class="hybrid-divider" points="414.1,629.1 424.1,576.8 473.2,567.9"/>
    <text class="hybrid-title"><textPath href="#path-connect" startOffset="50%" text-anchor="middle">CONNECT</textPath></text>
    <text class="hybrid-title"><textPath href="#path-act" startOffset="50%" text-anchor="middle">ACT</textPath></text>
    <text class="hybrid-title"><textPath href="#path-perceive" startOffset="50%" text-anchor="middle">PERCEIVE</textPath></text>
  </g>

  <g class="centre">
    <circle class="centre-core" cx="560" cy="478" r="125"/>
    <text class="centre-name" x="560" y="450">VEXORDA</text>
    <text class="centre-name" x="560" y="492">LOGO</text>
    <text class="centre-name" x="560" y="534">HERE</text>
  </g>
</svg>
</body>
</html>
```